Business card design for holistic health care clinic

We need a double-sided business card design for our holistic health care clinic that integrates our logo design and also its color scheme. My business is called Valmira. It is an integrative medicine clinic. You have already done the logo for me. Please ensure an elegant and upscale design that is not cluttered, but still has all the necessary information (please see below for details).

Target Market(s)

Wellness, fitness, rehabilitation for educated, well-traveled open-minded clients who are focused on natural, organic, balanced and preventive healthcare and lifestyle.

Industry/Entity Type

Medical

Contact Information for Business Card

Modern, clean.

Number of Pages Required

1 page

Font styles to use
Serif
Sans Serif

Colors

Designer to choose colors to be used in the design.

Requirements
Must have
• Logo on one side, all other information on the other side.
• Other information should include:
• Tobias Wrenfeld - DOE, CPT, LMT
• 4100 East Marrow Drive
• Austin, TX 78119
• 512 555 0148
• 818 555 0192
• info@ValmiraHealth.example
• t.wrenfeld@ValmiraHealth.example
Nice to have
• Darker background on front - but not totally black - shaded/dark gray.

```html
<!DOCTYPE html>
<html lang="en">
<head>
<meta charset="utf-8">
<title>Valmira Business Card</title>
<link href="https://fonts.googleapis.com/css2?family=Nunito+Sans:wght@400;600;700;800&display=swap" rel="stylesheet">
<style>
  :root {
    --canvas-bg: #e9e7e3;
    --card-dark: #2a2b2d;
    --brand-blue: #1d9bd7;
    --brand-blue-deep: #0f86c4;
    --ink-dark: #25272a;
    --text-light: #f2f4f5;
  }
  * { margin: 0; padding: 0; box-sizing: border-box; }
  html, body { width: 1200px; height: 886px; overflow: hidden; }
  body {
    background: var(--canvas-bg);
    font-family: "Nunito Sans", sans-serif;
    position: relative;
  }
  .card {
    position: absolute;
    top: 145px;
    width: 340px;
    height: 596px;
    border-radius: 22px;
    overflow: hidden;
    box-shadow: 0 10px 28px rgba(0,0,0,0.18);
  }
  /* Front: contact side */
  .card-front {
    left: 230px;
    background: var(--card-dark);
    color: var(--text-light);
    text-align: center;
  }
  .front-brand {
    margin-top: 78px;
  }
  .brand-name {
    font-weight: 800;
    letter-spacing: 2px;
    line-height: 1;
  }
  .card-front .brand-name { color: var(--brand-blue); font-size: 56px; }
  .brand-descriptor {
    font-weight: 600;
    font-size: 15px;
    letter-spacing: 0.5px;
    margin-top: 6px;
  }
  .card-front .brand-descriptor { color: var(--brand-blue); }
  .person-name {
    margin-top: 62px;
    color: var(--brand-blue);
    font-size: 27px;
    font-weight: 800;
    text-transform: uppercase;
  }
  .person-credentials {
    color: var(--brand-blue);
    font-size: 13px;
    font-weight: 700;
    margin-top: 2px;
  }
  .divider {
    width: 22px;
    height: 2px;
    background: var(--brand-blue);
    margin: 16px auto;
  }
  .address, .contact-list {
    font-size: 14.5px;
    line-height: 1.4;
    font-weight: 600;
  }
  .contact-label { color: var(--brand-blue); font-weight: 700; }
  .front-band {
    position: absolute;
    left: 0; right: 0; bottom: 0;
    height: 72px;
    background: var(--brand-blue);
    display: flex;
    align-items: center;
    justify-content: center;
    color: #fff;
    font-weight: 800;
    font-size: 16px;
  }
  /* Back: logo side */
  .card-back {
    left: 630px;
    background: var(--brand-blue);
    color: var(--ink-dark);
    text-align: center;
  }
  .back-brand { margin-top: 92px; }
  .card-back .brand-name { font-size: 58px; color: var(--ink-dark); }
  .card-back .brand-descriptor { color: var(--ink-dark); }
  .back-mark {
    display: block;
    margin: 74px auto 0;
  }
  .back-band {
    position: absolute;
    left: 0; right: 0; bottom: 0;
    height: 78px;
    background: var(--card-dark);
    display: flex;
    align-items: center;
    justify-content: center;
    color: var(--brand-blue);
    font-weight: 700;
    font-size: 17px;
  }
</style>
</head>
<body>
  <section class="card card-front">
    <div class="front-brand">
      <div class="brand-name">VALMIRA</div>
      <div class="brand-descriptor">Integrative Holistic Medicine</div>
    </div>
    <div class="person-name">Tobias Wrenfeld</div>
    <div class="person-credentials">DOE, CPT, LMT</div>
    <div class="divider"></div>
    <div class="address">
      4100 East Marrow Drive<br>
      Austin, TX 78119
    </div>
    <div class="divider"></div>
    <div class="contact-list">
      <span class="contact-label">P:</span> 512 555 0148<br>
      <span class="contact-label">M:</span> 818 555 0192<br>
      <span class="contact-label">E:</span> t.wrenfeld@ValmiraHealth.example
    </div>
    <div class="front-band">www.ValmiraHealth.example</div>
  </section>

  <section class="card card-back">
    <div class="back-brand">
      <div class="brand-name">VALMIRA</div>
      <div class="brand-descriptor">Integrative Holistic Medicine</div>
    </div>
    <svg class="back-mark" width="150" height="150" viewBox="0 0 150 150" aria-hidden="true">
      <circle cx="75" cy="75" r="70" fill="var(--ink-dark)"/>
    </svg>
    <div class="back-band">helping the body help itself</div>
  </section>
</body>
</html>
```